Corvane Holdings , new business card design

investment firm with corporate clients . need double sided business card , vertical and horizontal options ,logo must be clear. prefer pantone colors only and sharp design. website also www.corvane.ae

Khalid Bin Tarrafi
Managing Director
Tel. +971 4 387 2940
Mobile +971 50 518 2403
khalid@corvane.ae
Q-Span Plaza, officw 18-B07, Warqa Gardens, Dubai

Contact Information for Business Card

Khalid Bin Tarrafi
Managing Director

Font styles to use
Serif

Colors

Designer to choose colors to be used in the design.

```html
<!DOCTYPE html>
<html lang="en">
<head>
<meta charset="utf-8">
<title>Corvane Holdings — Business Card</title>
<link rel="stylesheet" href="https://fonts.googleapis.com/css2?family=Lato:wght@300;400;700&display=swap">
<style>
  :root {
    --backdrop: #e9e9eb;
    --card-dark: #0b0e15;
    --card-light: #ffffff;
    --brand-blue: #4a6f94;
    --ink: #2a2a2e;
    --ink-soft: #55565c;
    --paper-text: #f4f4f6;
  }
  * { margin: 0; padding: 0; box-sizing: border-box; }
  html, body {
    width: 1200px; height: 960px; overflow: hidden;
    background: var(--backdrop);
    font-family: "Lato", Arial, sans-serif;
  }
  .sheet {
    width: 1200px; height: 960px;
    display: flex; flex-direction: column; align-items: center; justify-content: center;
    gap: 40px;
  }
  .card {
    width: 700px; height: 400px; position: relative; overflow: hidden;
    box-shadow: 0 6px 18px rgba(0,0,0,.15);
  }

  /* Front */
  .card--front {
    background: var(--card-dark);
    display: flex; flex-direction: column; align-items: center; justify-content: center;
  }
  .wordmark {
    display: flex; align-items: center; gap: 16px;
    font-weight: 300; text-transform: uppercase;
  }
  .wordmark__square { width: 14px; height: 14px; background: currentColor; }
  .wordmark__name { font-size: 44px; letter-spacing: 10px; line-height: 1; }
  .card--front .wordmark { color: var(--paper-text); }
  .website {
    margin-top: 42px; color: var(--paper-text);
    font-size: 22px; letter-spacing: 4px;
  }

  /* Back */
  .card--back { background: var(--card-light); }
  .card--back .wordmark {
    color: var(--ink); position: absolute; top: 62px; left: 0; right: 0; justify-content: center;
  }
  .card--back .wordmark__name { font-size: 36px; letter-spacing: 8px; }
  .name-band {
    position: absolute; top: 150px; left: 0; right: 0; height: 80px;
    background: var(--brand-blue); color: #fff; text-align: center;
    display: flex; flex-direction: column; justify-content: center; gap: 4px;
  }
  .name-band__name { font-weight: 700; font-size: 21px; letter-spacing: 1px; text-transform: uppercase; }
  .name-band__title { font-weight: 300; font-size: 20px; letter-spacing: 1px; text-transform: uppercase; }
  .details {
    position: absolute; top: 262px; left: 0; right: 0;
    display: flex; justify-content: center;
    color: var(--ink-soft); font-size: 17px; line-height: 27px;
  }
  .address { text-align: right; padding-right: 18px; width: 330px; }
  .divider { width: 1px; background: #c9c9cc; }
  .contacts { list-style: none; padding-left: 18px; width: 330px; }
  .contacts li { display: flex; align-items: center; gap: 8px; }
  .contacts svg { width: 15px; height: 15px; fill: var(--brand-blue); flex: none; }
</style>
</head>
<body>
<main class="sheet">
  <section class="card card--front" aria-label="Card front">
    <div class="wordmark">
      <span class="wordmark__square"></span>
      <span class="wordmark__name">Corvane Holdings</span>
    </div>
    <p class="website">www.corvane.ae</p>
  </section>

  <section class="card card--back" aria-label="Card back">
    <div class="wordmark">
      <span class="wordmark__square"></span>
      <span class="wordmark__name">Corvane Holdings</span>
    </div>
    <div class="name-band">
      <p class="name-band__name">Khalid Bin Tarrafi</p>
      <p class="name-band__title">Managing Director</p>
    </div>
    <div class="details">
      <address class="address" style="font-style:normal">
        Q-Span Plaza<br>officw 18-B07<br>Warqa Gardens, Dubai
      </address>
      <span class="divider"></span>
      <ul class="contacts">
        <li>
          <svg viewBox="0 0 16 16" aria-hidden="true"><path d="M3.5 1.5l2.5 0 1 3.5-1.7 1.2a8 8 0 0 0 4.5 4.5L11 9l3.5 1v2.5c0 1-1 2-2 2A11 11 0 0 1 1.5 3.5c0-1 1-2 2-2z"/></svg>
          +971 4 387 2940
        </li>
        <li>
          <svg viewBox="0 0 16 16" aria-hidden="true"><path d="M4.5 0.5h7a1 1 0 0 1 1 1v13a1 1 0 0 1-1 1h-7a1 1 0 0 1-1-1v-13a1 1 0 0 1 1-1zm.8 2v9h5.4v-9zm2.7 10a1 1 0 1 0 0 2 1 1 0 0 0 0-2z"/></svg>
          +971 50 518 2403
        </li>
        <li>
          <svg viewBox="0 0 16 16" aria-hidden="true"><path d="M1 3.5h14v9H1zm1.4 1.2L8 9l5.6-4.3z"/></svg>
          khalid@corvane.ae
        </li>
      </ul>
    </div>
  </section>
</main>
</body>
</html>
```